Business Card Design for Training Business

Clear Path Coaching is a new business that delivers training and other services with a focus on topics related to mental health and wellbeing, for example, Wellmind Response Course, Resilience etc. We have a strong focus on evidence-based psychology and neuroscience. I have a logo which I will upload with the brief, so please consider colours that work well with the logo.
Target Market(s)
Adults, workplaces (particularly government and not-for-profits)
Industry/Entity Type
Business
Contact Information for Business Card
Head Strong TrainingSamantha SellwoodDirector0438 770 850sam@headstrongtraining.com.auwww.headstrongtraining.com.au

```html
<!DOCTYPE html>
<html lang="en">
<head>
<meta charset="utf-8">
<title>Clear Path Coaching – Business Card</title>
<link rel="stylesheet" href="https://fonts.googleapis.com/css2?family=Open+Sans:wght@300;400;600;700&display=swap">
<style>
  :root {
    --backdrop: #e9e7e3;
    --card: #f6f5f1;
    --teal: #36b5ad;
    --ink: #111111;
    --brand-grey: #6e6e6e;
  }
  * { box-sizing: border-box; margin: 0; padding: 0; }
  html, body {
    width: 1200px;
    height: 857px;
    overflow: hidden;
    background: var(--backdrop);
    font-family: "Open Sans", Arial, sans-serif;
  }
  .card {
    position: absolute;
    left: 100px;
    top: 123px;
    width: 1000px;
    height: 611px;
    background: var(--card);
    box-shadow: 0 10px 30px rgba(0,0,0,0.15);
    overflow: hidden;
  }
  .card__wave {
    position: absolute;
    inset: 0;
    width: 100%;
    height: 100%;
  }
  .brand {
    position: absolute;
    left: 40px;
    top: 170px;
    width: 340px;
    display: flex;
    flex-direction: column;
    align-items: center;
    gap: 28px;
  }
  .brand__mark {
    width: 130px;
    height: 130px;
    border-radius: 50%;
    border: 3px solid var(--teal);
  }
  .brand__name {
    font-weight: 300;
    font-size: 31px;
    letter-spacing: 1px;
    color: var(--brand-grey);
    white-space: nowrap;
  }
  .contact {
    position: absolute;
    left: 580px;
    top: 120px;
    width: 400px;
    text-align: center;
    color: var(--ink);
  }
  .contact__name {
    font-weight: 600;
    font-size: 40px;
    line-height: 1.2;
  }
  .contact__role {
    font-weight: 600;
    font-size: 27px;
    margin-top: 4px;
    margin-bottom: 34px;
  }
  .contact__line {
    font-weight: 400;
    font-size: 24px;
    line-height: 1.45;
    white-space: nowrap;
  }
</style>
</head>
<body>
  <main class="card">
    <svg class="card__wave" viewBox="0 0 1000 611" aria-hidden="true">
      <path d="M392 -10 C 398 190, 460 260, 555 360 C 640 450, 660 520, 690 621"
            fill="none" stroke="var(--teal)" stroke-width="26"/>
    </svg>

    <section class="brand">
      <div class="brand__mark"></div>
      <div class="brand__name">Clear Path Coaching</div>
    </section>

    <section class="contact">
      <h1 class="contact__name">Rebecca Tanfield</h1>
      <p class="contact__role">Director</p>
      <p class="contact__line">0491 362 517</p>
      <p class="contact__line">bec@clearpathcoaching.example.au</p>
      <p class="contact__line">www.clearpathcoaching.example.au</p>
    </section>
  </main>
</body>
</html>
```